New business card/stationary for a consulting company

I am looking for a clean and very professional looking business card for my consulting company as well as corresponding stationary. I am uploading our logo. I like simple and powerful for the feel. No graphics but I am open on everything else. Below is my contact information but would like the final to be in a version I can add my employees information into and print. Thank you.

Daniel Whitcombe
dan@ferncliffadvisory.com
2870 North 9th Avenue, Summit Floor, Elm Ridge, Illinois 60531
www.ferncliffadvisory.com

Industry/Entity Type

Consulting

Contact Information for Business Card

Daniel Whitcombe
dan@ferncliffadvisory.com
www.ferncliffadvisory.com

Font styles to use
Serif
Sans Serif

Requirements
Must have
• Our logo and the business card details.
Nice to have
• our website www.ferncliffadvisory.com

```html
<!DOCTYPE html>
<html lang="en">
<head>
<meta charset="utf-8">
<title>Ferncliff Advisory – Business Card</title>
<link rel="stylesheet" href="https://fonts.googleapis.com/css2?family=Questrial&family=Roboto:wght@400;700&display=swap">
<style>
  :root {
    --navy: #03035f;
    --paper: #f4f4f4;
    --ink-grey: #5a5a5a;
    --silver: #e2e2e6;
    --backdrop: #e9e7e4;
    --white: #ffffff;
  }
  * { margin: 0; padding: 0; box-sizing: border-box; }
  html, body {
    width: 1200px;
    height: 960px;
    overflow: hidden;
    background: var(--backdrop);
  }
  .canvas {
    position: relative;
    width: 1200px;
    height: 960px;
  }
  .card {
    position: absolute;
    width: 600px;
    height: 343px;
    box-shadow: 0 2px 6px rgba(0,0,0,0.25);
  }

  /* Front */
  .card-front {
    left: 302px;
    top: 129px;
    background: var(--paper);
  }
  .brand-square {
    position: absolute;
    left: 143px;
    top: 49px;
    width: 110px;
    height: 50px;
    background: var(--navy);
  }
  .brand-name {
    position: absolute;
    left: 44px;
    top: 110px;
    font-family: "Questrial", sans-serif;
    font-size: 24px;
    letter-spacing: 1.2px;
    color: var(--navy);
    white-space: nowrap;
  }
  .address {
    position: absolute;
    left: 44px;
    top: 225px;
    font-family: "Roboto", sans-serif;
    font-size: 14px;
    line-height: 18px;
    color: var(--ink-grey);
    font-style: normal;
  }
  .website {
    display: block;
    margin-top: 4px;
    font-weight: 700;
    letter-spacing: 0.2px;
  }
  .name-band {
    position: absolute;
    left: 334px;
    top: 239px;
    width: 266px;
    height: 59px;
    background: var(--navy);
  }
  .name-band::before {
    content: "";
    position: absolute;
    left: 4px;
    top: 0;
    width: 4px;
    height: 100%;
    background: var(--paper);
  }
  .person-name {
    position: absolute;
    left: 28px;
    top: 8px;
    font-family: "Questrial", sans-serif;
    font-size: 17px;
    font-weight: 700;
    letter-spacing: 1px;
    color: var(--white);
    white-space: nowrap;
  }
  .person-email {
    position: absolute;
    right: 30px;
    top: 31px;
    font-family: "Roboto", sans-serif;
    font-size: 14px;
    color: var(--white);
    white-space: nowrap;
  }

  /* Back */
  .card-back {
    left: 300px;
    top: 488px;
    background: var(--navy);
  }
  .back-square {
    position: absolute;
    left: 228px;
    top: 117px;
    width: 139px;
    height: 64px;
    background: var(--silver);
  }
  .back-name {
    position: absolute;
    left: 0;
    right: 0;
    top: 193px;
    text-align: center;
    font-family: "Questrial", sans-serif;
    font-size: 31px;
    letter-spacing: 1.5px;
    color: var(--silver);
    white-space: nowrap;
  }
</style>
</head>
<body>
  <main class="canvas">
    <section class="card card-front">
      <div class="brand-square"></div>
      <div class="brand-name">FERNCLIFF ADVISORY</div>
      <address class="address">
        2870 North 9th Avenue<br>
        Summit Floor, Elm Ridge<br>
        Illinois 60531
        <span class="website">FERNCLIFFADVISORY.COM</span>
      </address>
      <div class="name-band">
        <div class="person-name">DANIEL WHITCOMBE</div>
        <div class="person-email">dan@ferncliffadvisory.com</div>
      </div>
    </section>

    <section class="card card-back">
      <div class="back-square"></div>
      <div class="back-name">FERNCLIFF ADVISORY</div>
    </section>
  </main>
</body>
</html>
```